Calm Harbor Bodywork business is seeking a Business Card Design

We are a new natural therapy business that needs a Business Card Design with an appointment card on the back.

We offer Myotherapy (muscle therapy) services and have a strong focus and commitment to helping people relieve pain and restore movement to their bodies.

I am attaching my business logo for you information.

Business card must contain my logo and have space for name, title, qualifications, phone number, email, web address

Appointment Card on the back of the card must contain space to write next appointment date, time and name of therapist and cancellation policy.

Cancellation Policy
Minimum of 24hrs notice is required prior to appointment time or full treatment fees with apply.

```html
<!DOCTYPE html>
<html lang="en">
<head>
<meta charset="utf-8">
<title>Harborside Myotherapy – Business &amp; Appointment Card</title>
<link href="https://fonts.googleapis.com/css2?family=Lato:wght@400;700;900&display=swap" rel="stylesheet">
<style>
  :root{
    --bg:#2b2b2b;
    --card:#ffffff;
    --card-edge:#eeeeee;
    --red:#b5172f;
    --ink:#1b1b1b;
    --muted:#555555;
    --box:#d9546a;
  }
  *{box-sizing:border-box;margin:0;padding:0}
  html,body{width:1200px;height:900px;overflow:hidden;background:var(--bg)}
  body{font-family:"Lato",sans-serif;color:var(--ink);position:relative}
  .card{position:absolute;left:260px;width:680px;height:400px;border-radius:22px;
    background:linear-gradient(160deg,var(--card) 0%,var(--card-edge) 100%);overflow:hidden}
  .card--back{top:30px}
  .card--front{top:470px}

  /* back: appointment card */
  .appt-title{position:absolute;left:40px;top:34px;background:var(--red);color:#fff;
    font-weight:900;font-size:20px;letter-spacing:.5px;padding:5px 14px}
  .field{position:absolute;left:40px;font-size:18px;color:var(--ink);font-weight:700}
  .field span{font-weight:400;color:var(--muted);letter-spacing:2px}
  .field--date{top:100px}
  .field--time{top:100px;left:360px}
  .days{position:absolute;left:40px;top:160px;display:flex;gap:28px}
  .day{display:flex;align-items:center;gap:8px;font-weight:900;font-size:20px}
  .day i{display:block;width:28px;height:22px;border:2px solid var(--box);border-radius:5px}
  .field--therapist{top:220px}
  .policy{position:absolute;left:0;right:0;top:272px;text-align:center}
  .policy-label{display:inline-block;background:var(--red);color:#fff;font-weight:700;
    font-size:18px;padding:4px 12px;letter-spacing:.5px}
  .policy-text{margin-top:12px;font-size:17px;line-height:1.35;color:var(--ink)}

  /* front: business card */
  .person{position:absolute;left:46px;top:118px}
  .person-name{color:var(--red);font-weight:900;font-size:30px;letter-spacing:.3px}
  .person-role{font-weight:700;font-size:19px;margin-top:2px}
  .brand{position:absolute;right:44px;top:48px;display:flex;align-items:center;gap:12px}
  .brand-mark{width:40px;height:40px;background:var(--red)}
  .brand-name{color:var(--red);font-weight:700;font-size:30px}
  .mission{position:absolute;right:44px;top:196px;text-align:center;color:var(--red);
    font-weight:700;font-size:18px;line-height:1.35}
  .contacts{position:absolute;left:46px;bottom:36px;font-size:19px}
  .contact{display:flex;align-items:center;gap:14px;margin-top:10px;font-weight:700}
  .contact svg{width:24px;height:20px;flex:none}
  .contact--web{font-weight:900;font-size:21px;margin-top:14px}
  .contact--web em{font-style:normal;color:var(--red)}
</style>
</head>
<body>

<section class="card card--back" aria-label="Appointment card">
  <div class="appt-title">NEXT APPOINTMENT</div>
  <div class="field field--date">DATE: <span>..........................</span></div>
  <div class="field field--time">TIME: <span>.....................</span></div>
  <div class="days">
    <div class="day">Mon <i></i></div>
    <div class="day">Tue <i></i></div>
    <div class="day">Wed <i></i></div>
    <div class="day">Thu <i></i></div>
    <div class="day">Fri <i></i></div>
  </div>
  <div class="field field--therapist">THERAPIST: <span>.................................................</span></div>
  <div class="policy">
    <div class="policy-label">CANCELLATION POLICY</div>
    <p class="policy-text">Minimum of 24hrs notice is required prior to appointment time or full<br>treatment fees with apply</p>
  </div>
</section>

<section class="card card--front" aria-label="Business card">
  <div class="brand">
    <div class="brand-mark"></div>
    <div class="brand-name">Harborside Myotherapy</div>
  </div>
  <div class="person">
    <div class="person-name">YOUR NAME</div>
    <div class="person-role">DESIGNATION</div>
  </div>
  <p class="mission">Assists you to overcome<br>Acute &amp; Chronic pain &amp; injury<br>through Calm Harbor Bodywork</p>
  <div class="contacts">
    <div class="contact">
      <svg viewBox="0 0 24 20" aria-hidden="true"><path fill="#b5172f" d="M2 6c0-3 4-4 10-4s10 1 10 4v2h-5V6H7v2H2z"/><rect x="5" y="9" width="14" height="9" rx="2" fill="#b5172f"/></svg>
      +61 400 555 012
    </div>
    <div class="contact">
      <svg viewBox="0 0 24 20" aria-hidden="true"><rect x="1" y="3" width="22" height="14" fill="#b5172f"/><path d="M1 3l11 8 11-8" fill="none" stroke="#fff" stroke-width="1.6"/></svg>
      Info@harborsidemyo.com.au
    </div>
    <div class="contact contact--web">www.<em>harborsidemyo</em>.com.au</div>
  </div>
</section>

</body>
</html>
```